Lotstallmart.com Webpage Design

Design Brief for lotstallmart.com (Copy of Brief also in attached Word file)

Name of Website- lotstallmart.com (existing logo and look & feel of website to be changed)

Logo - Finalised. The logo files are attached with the brief as “logo.jpeg”. The “Blue- Grey” version of the logo is for use on lighter backgrounds and the “Orange-White” version of the logo is for use on darker backgrounds. (A full Black version of the logo is also attached). Both versions may be used in different parts of the website. All attached files are in .png format.
Status - The website in functional and is undergoing user trials. However, we want to improve the look & feel of the website so at it seems
a. cotemporary,
b. Easy to Navigate
c. professional and
d. Vibrant.

Please visit ‘lotstallmart.com’ to check out the website and its functionalities – please use it only as a reference for the features & functions to be provided, however the designer should use a ‘Free Hand’ in designing the composition of various parts of the webpage without getting too influenced by the existing design

Objective of the Website ‘lotstallmart.com –
a. It is a portal focussed on listing of ‘Retail’ specific real-estate properties by developers, owners and realty brokers. The properties shall listed under the following four categories-
i. Retail Malls
ii. Shopping Complexes
iii. High-street shops
iv. Retail Warehouses
*refer lotstallmart.com for better clarity

b. The abovementioned properties shall be listed either for ‘Sale’ or ‘rent\lease’ or both

c. Users shall visit the site in case they wish to acquire a retail \ shop space either on ‘sale’ or ‘rent’. These Users would be able to specify the ‘Search Criteria’ through the tool-bars provided on the website – the ‘Search Criteria’ shall comprise of ‘Type of space category’, ‘City’, ‘Locality’, transaction type ie ‘Rent \ Sale’ and ‘Area Range’

d. The main revenue model for the website shall be listing fee ( or advertising charges ) payable by those listing their properties on the website.

Three Main Pages of Website (lotstallmart.com) that need to be designed -
a. Main Home Page (visit the web link - http://lotstallmart.com/ ) - The main home page has the “Search Toolbar” for specifying of Search Criteria by the User. It shall also have the following features & functions-
i. Main Advertising Banner
ii. Featured Projects
iii. New Launches
iv. Toolbar with buttons – ‘Advertise with Us’, ‘Listings Alert’, ‘Mart Wizards’, ‘Advertiser Login’

b. Property Listings Page (visit the web link - http://lotstallmart.com/gurgaon-in-india ) - The List of property options that match the Criteria specified by the ‘User’ get displayed on this page.

c. Property Detail Page - When the ‘User’ clicks on the “More….” Button on the ‘Property Listings Page’ (given in point b. above) the web page with the details of the property opens. (For Example – visit the web link - http://lotstallmart.com/vorne-Shopping-Complex-vorne-quadrion-gurgaon-636 )

Note:- Please refer to attached ‘Shopping’ related images the designer may use them on the website to provide a look & feel of retail if required – either separately or rotate in a single window

Target Market(s)

Retailers & Investors looking for retail space, Real Estate Brokers, Developers

Industry/Entity Type

Advertising

Number of Pages Required

3 page

Requirements
Must have
• Refer to existing site lotstallmart.com -- all the existing functionalities are a must have.
Nice to have
• The Designer may use the retail related images on the website if required for making it more vibrant. Refer attached images Shopping(1-6).jpg

```html
<!DOCTYPE html>
<html lang="en">
<head>
<meta charset="utf-8">
<title>Lotstallmart.com – Retail Space Portal</title>
<link href="https://fonts.googleapis.com/css2?family=Dosis:wght@400;500;600;700&family=Open+Sans:wght@400;600;700&display=swap" rel="stylesheet">
<style>
:root{
  --orange:#f2a631;
  --orange-dark:#e0921c;
  --orange-soft:#f7cf8c;
  --ink:#1f1f1f;
  --ink-2:#2b2b2b;
  --text:#444;
  --muted:#8a8a8a;
  --paper:#ffffff;
  --paper-2:#f1f1f1;
  --line:#dcdcdc;
}
*{box-sizing:border-box;margin:0;padding:0}
html,body{width:1200px;height:3445px;overflow:hidden}
body{position:relative;background:var(--paper);font-family:"Open Sans",Arial,sans-serif;color:var(--text)}
.abs{position:absolute}
.head-font{font-family:"Dosis","Arial Narrow",sans-serif}

/* header */
.site-header{left:0;top:0;width:1200px;height:106px;background:var(--ink)}
.brand{left:22px;top:20px;display:flex;align-items:center;gap:10px}
.brand-dot{width:34px;height:34px;border-radius:50%;background:var(--orange)}
.brand-name{font-family:"Dosis",sans-serif;font-weight:700;font-size:38px;color:#fff;line-height:1}
.brand-tag{left:66px;top:64px;font-size:9px;color:#bbb;letter-spacing:1px;text-transform:uppercase}
.nav{left:416px;top:0;height:106px;display:flex}
.nav-home{width:101px;height:106px;background:var(--orange);display:flex;align-items:center;justify-content:center}
.nav-item{width:150px;height:106px;border-right:1px solid #3a3a3a;color:#fff;font-family:"Dosis",sans-serif;font-size:18px;line-height:1.1;text-align:center;padding-top:36px;text-transform:uppercase}
.nav-item small{display:block;text-transform:none;font-size:16px;color:#ddd}
.nav-item:nth-child(4){width:115px}
.register{left:970px;top:14px;font-size:14px;color:#fff;text-decoration:underline}
.login-btn{left:956px;top:40px;width:172px;height:40px;background:var(--orange);color:#fff;font-size:15px;display:flex;align-items:center;justify-content:center}

/* hero */
.hero{left:0;top:106px;width:1200px;height:563px;background:linear-gradient(135deg,#6b5a4c 0%,#b39b83 35%,#e3d6c6 55%,#8a6e5a 80%,#4e3c32 100%)}
.hero-title{left:110px;top:280px;font-family:"Dosis",sans-serif;font-size:46px;color:#fff;font-weight:500}
.hero-sub{left:110px;top:338px;font-size:22px;color:#fff;line-height:1.3}
.hero-arrow{top:350px;width:40px;height:40px;background:rgba(0,0,0,.55);display:flex;align-items:center;justify-content:center}

/* welcome */
.welcome{left:0;top:669px;width:1200px;height:456px;background:var(--paper-2)}
.welcome-title{left:84px;top:705px;font-family:"Dosis",sans-serif;font-size:36px;color:var(--ink-2);font-weight:600}
.welcome-title span{color:var(--orange)}
.welcome-text{left:84px;top:765px;width:450px;font-size:14px;line-height:1.65;color:#666}
.roles{left:84px;top:928px;display:flex;gap:44px;font-size:14px;color:#555}
.roles span::before{content:"»";color:var(--orange);margin-right:8px}
.btn{background:var(--orange);color:#fff;font-size:14px;display:flex;align-items:center;justify-content:center}
.read-more{left:86px;top:1005px;width:166px;height:34px}

.finder{left:563px;top:706px;width:563px;height:351px;background:var(--ink-2);padding:28px 40px}
.finder h2{font-family:"Dosis",sans-serif;font-size:42px;color:#fff;font-weight:700;line-height:1}
.finder h2 span{font-size:26px;color:var(--orange);font-weight:500}
.field{position:absolute;width:240px}
.field label{display:block;font-size:10px;color:#fff;text-transform:uppercase;margin-bottom:6px}
.field div{height:24px;background:#999;font-size:10px;color:#ddd;padding:5px 8px}
.search-btn{left:346px;top:270px;width:166px;height:34px;position:absolute}

.services{left:200px;top:1157px;width:800px;text-align:center;font-size:14px;line-height:1.6;color:#555}

/* categories */
.cat{top:1235px;height:272px;overflow:hidden}
.cat .ph{position:absolute;inset:0}
.cat .cap{position:absolute;left:0;right:0;bottom:0;height:36px;background:var(--orange);color:#fff;font-family:"Dosis",sans-serif;font-size:18px;font-weight:600;display:flex;align-items:center;justify-content:center;text-transform:uppercase}

/* featured */
.band{left:0;top:1559px;width:1200px;height:112px;background:var(--orange);display:flex;align-items:center;justify-content:center;font-family:"Dosis",sans-serif;font-size:38px;color:#fff;font-weight:600}
.tabs{left:0;top:1671px;width:1200px;height:60px;background:var(--orange-soft);display:flex;align-items:center;padding-left:135px;font-family:"Dosis",sans-serif;font-size:19px;color:var(--ink-2);text-transform:uppercase;font-weight:600}
.tab{padding:0 34px}
.tab.active{background:var(--orange);color:#fff;height:60px;display:flex;align-items:center;padding:0 34px}

.card{width:318px}
.card .img{position:relative;height:253px}
.card .ph{position:absolute;inset:0}
.city{position:absolute;top:0;right:36px;height:36px;padding:0 16px;background:#333;color:#fff;font-size:15px;display:flex;align-items:center}
.tagbox{position:absolute;top:0;right:0;width:36px;height:36px;background:var(--orange);display:flex;align-items:center;justify-content:center}
.deal{position:absolute;left:0;right:0;bottom:0;height:34px;background:#333;color:#fff;font-size:14px;font-weight:700;display:flex;align-items:center;padding-left:10px;letter-spacing:1px}
.card h3{font-family:"Dosis",sans-serif;font-size:19px;color:var(--ink-2);font-weight:700;letter-spacing:1px;margin-top:12px;text-transform:uppercase}
.card p{font-family:"Dosis",sans-serif;font-size:18px;color:#444;letter-spacing:1px;text-transform:uppercase;margin-top:6px}
.card.sel .img{outline:5px solid var(--orange);outline-offset:-5px}
.card.sel .deal{background:var(--orange)}
.pager{top:2420px;width:38px;height:38px;background:#333;display:flex;align-items:center;justify-content:center}

/* launches */
.launch-bg{left:0;top:2498px;width:1200px;height:373px;background:var(--paper-2)}
.sec-title{width:1200px;left:0;text-align:center;font-family:"Dosis",sans-serif;font-size:36px;color:var(--ink-2);font-weight:600}
.launch{top:2584px;width:312px;height:216px}
.launch .ph{position:absolute;inset:0}
.launch .lbl{position:absolute;left:0;right:0;bottom:14px;text-align:center;font-family:"Dosis",sans-serif;color:#fff;font-size:17px;font-weight:700;line-height:1.1;text-transform:uppercase}
.launch.sel{outline:5px solid var(--orange);outline-offset:-5px}
.side-arrow{display:flex;align-items:center;justify-content:center;width:24px;height:30px}
.view-all{left:518px;top:2826px;width:166px;height:34px}

/* partners */
.partner{top:3000px;width:82px;height:48px;border-radius:4px}

/* footer */
.site-footer{left:0;top:3152px;width:1200px;height:293px;background:var(--ink)}
.foot-h{font-family:"Dosis",sans-serif;font-size:22px;color:#fff;font-weight:600}
.foot-p{font-size:12px;line-height:1.6;color:#8c8c8c}
.ghost-btn{border:1px solid #666;color:#ccc;font-size:13px;display:flex;align-items:center;justify-content:center}
.social{width:34px;height:34px;border:1px solid #777;display:flex;align-items:center;justify-content:center}
.social span{width:12px;height:12px;background:#ccc}
.input{background:#3a3a3a;height:30px;color:#999;font-size:12px;padding:7px 10px}
</style>
</head>
<body>

<header class="abs site-header">
  <div class="abs brand"><div class="brand-dot"></div><div class="brand-name">lotstallmart</div></div>
  <div class="abs brand-tag">India's leading portal for retail space</div>
  <nav class="abs nav">
    <div class="nav-home">
      <svg width="38" height="34" viewBox="0 0 38 34"><path d="M19 2 2 17h5v15h9v-9h6v9h9V17h5z" fill="#fff"/></svg>
    </div>
    <div class="nav-item">Advertise<small>with us</small></div>
    <div class="nav-item">Listings<small>alert</small></div>
    <div class="nav-item">Mart<small>Wizards</small></div>
  </nav>
  <div class="abs register">New advertiser Register</div>
  <div class="abs login-btn">Advertiser login</div>
</header>

<section class="abs hero" role="img" aria-label="Banner photo of a bright fashion store interior with clothing racks and sale signs"></section>
<div class="abs hero-title">A wide variety of storage spaces!</div>
<div class="abs hero-sub">Looking for stylish, independent or city centre location?<br>We help you find it quickly.</div>
<div class="abs hero-arrow" style="left:26px"><svg width="14" height="18"><path d="M11 2 3 9l8 7" stroke="#fff" stroke-width="3" fill="none"/></svg></div>
<div class="abs hero-arrow" style="left:1134px"><svg width="14" height="18"><path d="M3 2l8 7-8 7" stroke="#fff" stroke-width="3" fill="none"/></svg></div>

<section class="abs welcome"></section>
<h1 class="abs welcome-title">WELCOME TO <span>LOTSTALLMART!</span></h1>
<p class="abs welcome-text">Lotstallmart.com is a specialised web based platform for retail space, featuring properties across India under various formats such as retail malls, shopping complexes, high-street shops and retail warehouses. Lotstallmart.com is useful to various categories of users as follows</p>
<div class="abs roles"><span>Developers</span><span>Retailers</span><span>Investors</span><span>Brokers</span></div>
<div class="abs btn read-more">Read more</div>

<form class="abs finder">
  <h2>FIND <span>a location</span></h2>
  <div class="field" style="left:40px;top:90px"><label>Select Category</label><div>Shopping Complex</div></div>
  <div class="field" style="left:306px;top:90px"><label>Select State/County</label><div>Haryana</div></div>
  <div class="field" style="left:40px;top:166px"><label>Select Locality/Micro Market</label><div>Sector 29</div></div>
  <div class="field" style="left:306px;top:166px"><label>Transaction Type</label><div>Rent</div></div>
  <div class="field" style="left:40px;top:242px"><label>Enter Keywords</label><div>Project name, Developer</div></div>
  <div class="btn search-btn">Search</div>
</form>

<p class="abs services">Our services go beyond just providing sale, rent and lease for exclusive shopspaces. Lotstallmart.com is an initiative by a team of Engineers, Architects and Marketing professionals with varied experience in the Real Estate and IT services Industries.</p>

<div class="abs cat" style="left:72px;width:252px"><div class="ph" role="img" aria-label="Photo of a multi-level retail mall interior" style="background:linear-gradient(160deg,#c9a77b,#8b6a48 60%,#5b4634)"></div><div class="cap">Retail Malls</div></div>
<div class="abs cat" style="left:359px;width:230px"><div class="ph" role="img" aria-label="Photo of a shopping complex storefront with sale banners" style="background:linear-gradient(160deg,#e4d4b0,#b89a62 55%,#6f5a3a)"></div><div class="cap">Shopping Complexes</div></div>
<div class="abs cat" style="left:626px;width:233px"><div class="ph" role="img" aria-label="Photo of a retail warehouse with tall stocked shelves" style="background:linear-gradient(160deg,#9db0c4,#6c7f94 55%,#3f4c5b)"></div><div class="cap">Retail Warehouses</div></div>
<div class="abs cat" style="left:896px;width:229px"><div class="ph" role="img" aria-label="Photo of a busy high-street shop front" style="background:linear-gradient(160deg,#b45b4a,#7a3a32 55%,#3c2422)"></div><div class="cap">High-Street Shops</div></div>

<div class="abs band">FEATURED PROJECTS</div>
<div class="abs tabs"><div class="tab active">All</div><div class="tab">Malls</div><div class="tab">Complexes</div><div class="tab">Street Shops</div><div class="tab">Warehouses</div></div>

<!-- featured row 1 -->
<article class="abs card sel" style="left:78px;top:1757px"><div class="img"><div class="ph" role="img" aria-label="Rendering of a shopping complex building" style="background:linear-gradient(180deg,#cfd6dc,#b9a28a 45%,#8f7a66)"></div><div class="city">SURAT</div><div class="tagbox"><svg width="16" height="16"><path d="M1 1h7l7 7-7 7-7-7z" fill="#fff"/></svg></div><div class="deal">SALE / RENT</div></div><h3>Veltra Arcade</h3><p>Shopping Complex</p></article>
<article class="abs card" style="left:437px;top:1757px"><div class="img"><div class="ph" role="img" aria-label="Rendering of a shopping complex courtyard" style="background:linear-gradient(180deg,#c9d3c4,#9aa48c 50%,#6e7665)"></div><div class="city">SURAT</div><div class="tagbox"><svg width="16" height="16"><path d="M1 1h7l7 7-7 7-7-7z" fill="#fff"/></svg></div><div class="deal">SALE / RENT</div></div><h3>Veltra Arcade</h3><p>Shopping Complex</p></article>
<article class="abs card" style="left:798px;top:1757px"><div class="img"><div class="ph" role="img" aria-label="Rendering of a shopping complex walkway" style="background:linear-gradient(180deg,#d4d8da,#a2a8aa 50%,#6f7578)"></div><div class="city">GURGAON</div><div class="tagbox"><svg width="16" height="16"><path d="M1 1h7l7 7-7 7-7-7z" fill="#fff"/></svg></div><div class="deal">SALE / RENT</div></div><h3>Norvane Plaza</h3><p>Shopping Complex</p></article>

<!-- featured row 2 -->
<article class="abs card" style="left:78px;top:2076px"><div class="img" style="height:221px"><div class="ph" role="img" aria-label="Rendering of a shopping complex building" style="background:linear-gradient(180deg,#cfd6dc,#b9a28a 45%,#8f7a66)"></div><div class="city">SURAT</div><div class="tagbox"><svg width="16" height="16"><path d="M1 1h7l7 7-7 7-7-7z" fill="#fff"/></svg></div><div class="deal">SALE / RENT</div></div><h3>Veltra Arcade</h3><p>Shopping Complex</p></article>
<article class="abs card" style="left:437px;top:2076px"><div class="img" style="height:221px"><div class="ph" role="img" aria-label="Rendering of a shopping complex courtyard" style="background:linear-gradient(180deg,#c9d3c4,#9aa48c 50%,#6e7665)"></div><div class="city">SURAT</div><div class="tagbox"><svg width="16" height="16"><path d="M1 1h7l7 7-7 7-7-7z" fill="#fff"/></svg></div><div class="deal">SALE / RENT</div></div><h3>Veltra Arcade</h3><p>Shopping Complex</p></article>
<article class="abs card" style="left:798px;top:2076px"><div class="img" style="height:221px"><div class="ph" role="img" aria-label="Rendering of a shopping complex walkway" style="background:linear-gradient(180deg,#d4d8da,#a2a8aa 50%,#6f7578)"></div><div class="city">GURGAON</div><div class="tagbox"><svg width="16" height="16"><path d="M1 1h7l7 7-7 7-7-7z" fill="#fff"/></svg></div><div class="deal">SALE / RENT</div></div><h3>Norvane Plaza</h3><p>Shopping Complex</p></article>

<div class="abs pager" style="left:1028px"><svg width="12" height="12"><path d="M8 1 3 6l5 5" stroke="#fff" stroke-width="2" fill="none"/></svg></div>
<div class="abs pager" style="left:1091px"><svg width="12" height="12"><path d="M4 1l5 5-5 5" stroke="#fff" stroke-width="2" fill="none"/></svg></div>

<!-- new launches -->
<section class="abs launch-bg"></section>
<h2 class="abs sec-title" style="top:2520px">NEW LAUNCHES</h2>
<div class="abs side-arrow" style="left:40px;top:2685px"><svg width="12" height="18"><path d="M10 2 3 9l7 7" stroke="#e0921c" stroke-width="3" fill="none"/></svg></div>
<div class="abs side-arrow" style="left:1136px;top:2685px"><svg width="12" height="18"><path d="M2 2l7 7-7 7" stroke="#e0921c" stroke-width="3" fill="none"/></svg></div>
<article class="abs launch sel" style="left:84px"><div class="ph" role="img" aria-label="Rendering of a new shopping complex" style="background:linear-gradient(180deg,#cfd6dc,#b9a28a 45%,#8f7a66)"></div><div class="city">SURAT</div><div class="tagbox"><svg width="16" height="16"><path d="M1 1h7l7 7-7 7-7-7z" fill="#fff"/></svg></div><div class="lbl">Veltra Arcade<br>Shopping Complex</div></article>
<article class="abs launch" style="left:443px"><div class="ph" role="img" aria-label="Rendering of a new shopping complex courtyard" style="background:linear-gradient(180deg,#c9d3c4,#9aa48c 50%,#6e7665)"></div><div class="city">SURAT</div><div class="tagbox"><svg width="16" height="16"><path d="M1 1h7l7 7-7 7-7-7z" fill="#fff"/></svg></div><div class="lbl">Veltra Arcade<br>Shopping Complex</div></article>
<article class="abs launch" style="left:804px"><div class="ph" role="img" aria-label="Rendering of a new shopping complex walkway" style="background:linear-gradient(180deg,#d4d8da,#a2a8aa 50%,#6f7578)"></div><div class="city">GURGAON</div><div class="tagbox"><svg width="16" height="16"><path d="M1 1h7l7 7-7 7-7-7z" fill="#fff"/></svg></div><div class="lbl">Norvane Plaza<br>Shopping Complex</div></article>
<div class="abs btn view-all">View all</div>

<!-- partners -->
<h2 class="abs sec-title" style="top:2920px">PARTNERS</h2>
<div class="abs side-arrow" style="left:40px;top:3010px"><svg width="12" height="18"><path d="M10 2 3 9l7 7" stroke="#e0921c" stroke-width="3" fill="none"/></svg></div>
<div class="abs side-arrow" style="left:1136px;top:3010px"><svg width="12" height="18"><path d="M2 2l7 7-7 7" stroke="#e0921c" stroke-width="3" fill="none"/></svg></div>
<div class="abs partner" style="left:204px;background:#3f5d9a"></div>
<div class="abs partner" style="left:306px;background:#d9dde3"></div>
<div class="abs partner" style="left:398px;background:#c94b3b"></div>
<div class="abs partner" style="left:496px;background:#e8e8e8"></div>
<div class="abs partner" style="left:616px;background:#3f5d9a"></div>
<div class="abs partner" style="left:714px;background:#d9dde3"></div>
<div class="abs partner" style="left:806px;background:#c94b3b"></div>
<div class="abs partner" style="left:904px;background:#e8e8e8"></div>

<!-- footer -->
<footer class="abs site-footer">
  <h4 class="abs foot-h" style="left:89px;top:30px">Editor's Choice</h4>
  <p class="abs foot-p" style="left:89px;top:78px;width:240px">A trusted catalog of retail properties handpicked by our editors, ranked on clear criteria such as design, location, developer and footfall. Go to check the full list.</p>
  <div class="abs ghost-btn" style="left:89px;top:238px;width:150px;height:30px">more</div>

  <h4 class="abs foot-h" style="left:416px;top:30px">Get in touch</h4>
  <div class="abs" style="left:416px;top:84px;display:flex;gap:10px">
    <div class="social"><span></span></div><div class="social"><span></span></div><div class="social"><span></span></div><div class="social"><span></span></div>
  </div>
  <p class="abs foot-p" style="left:416px;top:136px">Subscribe to our newsletter to stay update with what is new</p>
  <div class="abs input" style="left:416px;top:164px;width:418px">Email Address</div>
  <div class="abs ghost-btn" style="left:416px;top:216px;width:150px;height:30px">Subscribe</div>

  <h4 class="abs foot-h" style="left:900px;top:30px">Contact</h4>
  <svg class="abs" style="left:900px;top:80px" width="12" height="16"><path d="M6 1a5 5 0 0 0-5 5c0 4 5 9 5 9s5-5 5-9a5 5 0 0 0-5-5z" fill="#777"/></svg>
  <p class="abs foot-p" style="left:922px;top:76px;width:220px">Stallway House, Unit 12, 3rd Floor, Sector 9, Gurgaon 122001</p>
  <svg class="abs" style="left:900px;top:148px" width="12" height="14"><rect x="2" y="0" width="8" height="14" rx="2" fill="#777"/></svg>
  <p class="abs foot-p" style="left:922px;top:146px">Phone : 011-555-0142</p>
  <p class="abs foot-p" style="left:922px;top:232px;font-size:10px">Copyright © Lotstallmart.com<br>All rights reserved.</p>
</footer>

</body>
</html>
```